The Plate Compass

Cutting Through the Noise to What Actually Works.

Nutrition book

Target Market(s)

People looking to be or get healthy and eat right.

```html
<!DOCTYPE html>
<html lang="en">
<head>
<meta charset="utf-8">
<title>The Plate Compass – Cover</title>
<link href="https://fonts.googleapis.com/css2?family=Archivo+Black&family=Barlow+Condensed:wght@600;700&family=Rubik:wght@400;700&display=swap" rel="stylesheet">
<style>
  :root {
    --backdrop: #242424;
    --paper: #dcdad4;
    --ink: #26332f;
    --accent: #c2402b;
    --plate: #efeeea;
    --plate-rim: #d6d4ce;
    --tick: #3a3a3a;
    --knob-light: #fbfbfa;
    --knob-dark: #bdbbb6;
  }
  * { box-sizing: border-box; margin: 0; padding: 0; }
  html, body { width: 1200px; height: 1200px; overflow: hidden; }
  body { background: var(--backdrop); position: relative; }

  .cover {
    position: absolute; left: 190px; top: 20px;
    width: 820px; height: 1160px;
    background: var(--paper);
    overflow: hidden;
  }

  .title { position: absolute; left: 78px; top: 96px; color: var(--ink); }
  .title__the {
    font-family: "Archivo Black", sans-serif; font-size: 34px;
    color: var(--accent); letter-spacing: 2px; display: block; margin-bottom: 4px;
  }
  .title__main {
    font-family: "Archivo Black", sans-serif; font-size: 74px;
    line-height: 0.98; letter-spacing: 1px; text-transform: uppercase;
  }

  .dial { position: absolute; left: 30px; top: 330px; width: 600px; height: 600px; }
  .dial svg { position: absolute; inset: 0; }
  .dial__food {
    position: absolute; left: 132px; top: 132px; width: 336px; height: 336px;
    border-radius: 50%;
    background:
      radial-gradient(circle at 70% 28%, #c9602c 0 18%, transparent 32%),
      radial-gradient(circle at 28% 70%, #1f3a1e 0 20%, transparent 36%),
      radial-gradient(circle at 48% 45%, #d9b98a 0 22%, #b08357 45%, #5a5030 80%);
  }
  .dial__label {
    position: absolute; left: 0; right: 0; top: 560px; text-align: center;
    font-family: "Barlow Condensed", sans-serif; font-weight: 700;
    font-size: 46px; letter-spacing: 5px; color: var(--accent);
  }

  .controls {
    position: absolute; left: 590px; top: 250px; width: 210px;
    display: flex; flex-direction: column; align-items: center; gap: 28px;
  }
  .control { display: flex; flex-direction: column; align-items: center; gap: 14px; }
  .knob {
    position: relative; border-radius: 50%;
    background: radial-gradient(circle at 40% 35%, var(--knob-light), #e4e3df 55%, var(--knob-dark));
    box-shadow: 0 0 0 4px #cfcdc8, 0 0 0 6px #a9a7a2, 4px 8px 14px rgba(0,0,0,0.28);
  }
  .knob::after {
    content: ""; position: absolute; left: 50%; top: 10%;
    width: 3px; height: 18%; margin-left: -1.5px;
    background: var(--tick); border-radius: 2px;
  }
  .knob--xl { width: 104px; height: 104px; }
  .knob--lg { width: 88px; height: 88px; }
  .knob--md { width: 74px; height: 74px; }
  .knob--sm { width: 62px; height: 62px; }
  .knob--xs { width: 50px; height: 50px; }
  .control__label {
    font-family: "Barlow Condensed", sans-serif; font-weight: 700;
    font-size: 27px; letter-spacing: 1.5px; color: var(--ink); white-space: nowrap;
  }

  .tagline {
    position: absolute; left: 78px; top: 1010px;
    font-family: "Rubik", sans-serif; font-size: 30px; line-height: 1.25; color: var(--ink);
  }
  .tagline strong { color: var(--accent); font-weight: 700; display: block; }
</style>
</head>
<body>
  <main class="cover">
    <h1 class="title">
      <span class="title__the">THE</span>
      <span class="title__main">Plate<br>Compass</span>
    </h1>

    <section class="dial">
      <svg viewBox="0 0 600 600" aria-hidden="true">
        <defs>
          <filter id="plateShadow" x="-20%" y="-20%" width="140%" height="140%">
            <feDropShadow dx="4" dy="8" stdDeviation="8" flood-opacity="0.3"/>
          </filter>
        </defs>
        <g stroke="var(--tick)" stroke-width="2.5" stroke-linecap="round">
          <line x1="300" y1="26" x2="300" y2="42" transform="rotate(-64 300 300)"/>
          <line x1="300" y1="26" x2="300" y2="42" transform="rotate(-56 300 300)"/>
          <line x1="300" y1="26" x2="300" y2="42" transform="rotate(-48 300 300)"/>
          <line x1="300" y1="26" x2="300" y2="42" transform="rotate(-40 300 300)"/>
          <line x1="300" y1="26" x2="300" y2="42" transform="rotate(-32 300 300)"/>
          <line x1="300" y1="26" x2="300" y2="42" transform="rotate(-24 300 300)"/>
          <line x1="300" y1="26" x2="300" y2="42" transform="rotate(-16 300 300)"/>
          <line x1="300" y1="26" x2="300" y2="42" transform="rotate(-8 300 300)"/>
          <line x1="300" y1="26" x2="300" y2="42" transform="rotate(8 300 300)"/>
          <line x1="300" y1="26" x2="300" y2="42" transform="rotate(16 300 300)"/>
          <line x1="300" y1="26" x2="300" y2="42" transform="rotate(24 300 300)"/>
          <line x1="300" y1="26" x2="300" y2="42" transform="rotate(32 300 300)"/>
          <line x1="300" y1="26" x2="300" y2="42" transform="rotate(40 300 300)"/>
          <line x1="300" y1="26" x2="300" y2="42" transform="rotate(48 300 300)"/>
          <line x1="300" y1="26" x2="300" y2="42" transform="rotate(56 300 300)"/>
          <line x1="300" y1="26" x2="300" y2="42" transform="rotate(64 300 300)"/>
        </g>
        <line x1="300" y1="22" x2="300" y2="46" stroke="var(--accent)" stroke-width="7" stroke-linecap="round"/>
        <circle cx="300" cy="300" r="240" fill="var(--plate-rim)" filter="url(#plateShadow)"/>
        <circle cx="300" cy="300" r="232" fill="var(--plate)"/>
        <circle cx="300" cy="300" r="190" fill="none" stroke="#dfddd8" stroke-width="3"/>
      </svg>
      <div class="dial__food" role="img" aria-label="Photo of a plate of sliced grilled chicken, roasted sweet potato cubes and sautéed kale"></div>
      <p class="dial__label">CALORIES</p>
    </section>

    <section class="controls">
      <div class="control"><div class="knob knob--xl"></div><span class="control__label">PROTEIN</span></div>
      <div class="control"><div class="knob knob--lg"></div><span class="control__label">FOOD QUALITY</span></div>
      <div class="control"><div class="knob knob--md"></div><span class="control__label">MEAL TIMING</span></div>
      <div class="control"><div class="knob knob--sm"></div><span class="control__label">SUPPLEMENTS</span></div>
      <div class="control"><div class="knob knob--xs"></div><span class="control__label">NOISE / OFF</span></div>
    </section>

    <p class="tagline">Cutting Through the Noise <strong>to What Actually Works.</strong></p>
  </main>
</body>
</html>
```